VENTURE CAPITAL GROUP BUSINESS CARD DESIGN

Venture Capital Group based in SF looking for a bold business card design. No trendy colour explosion, 3D effects etc. Just "simple" optical effects. Works on your brain, keeps your eye focused and sticks to your mind.
Target Market(s)
Technology startups
Industry/Entity Type
Venture Capital
Contact Information for Business Card
DESMOND WHITLAKE
MANAGING PARTNER
187 FENWORTH ST SAN FRANCISCO, CA 94187
415.555.0142 O
415.555.0147 F
415.555.0193 C
desmond@veldtmoorcapital.ventures

```html
<!DOCTYPE html>
<html lang="en">
<head>
<meta charset="utf-8">
<title>Veldtmoor Capital Group – Business Card</title>
<link href="https://fonts.googleapis.com/css2?family=Crimson+Text:wght@400;600;700&display=swap" rel="stylesheet">
<style>
  :root {
    --backdrop: #1c1c1c;
    --card-dark: #1f2622;
    --card-dark-deep: #141a17;
    --card-light: #f4f4f4;
    --card-light-shade: #d9d9d9;
    --brand-green: #1f8a3b;
    --brand-green-deep: #166b2d;
    --ink: #1e1e1e;
    --rule: #b5b5b5;
  }
  * { margin: 0; padding: 0; box-sizing: border-box; }
  html, body {
    width: 1200px; height: 873px; overflow: hidden;
    background: var(--backdrop);
    font-family: "Crimson Text", Georgia, serif;
  }
  .stage { position: relative; width: 1200px; height: 873px; }

  .card {
    position: absolute;
    border-radius: 3px;
    box-shadow: 0 12px 30px rgba(0,0,0,.55);
    overflow: hidden;
  }

  /* front side */
  .card-front {
    left: 80px; top: 50px; width: 620px; height: 354px;
    background: linear-gradient(135deg, var(--card-dark) 0%, var(--card-dark-deep) 100%);
  }
  .card-front .brand { position: absolute; left: 0; right: 0; top: 135px; text-align: center; }

  .brand-name {
    display: flex; align-items: center; gap: 12px;
    color: var(--brand-green);
    font-weight: 600; font-size: 44px; letter-spacing: 1px; line-height: 1;
    white-space: nowrap;
  }
  .card-front .brand-name { justify-content: center; }
  .brand-dot { width: 22px; height: 22px; border-radius: 50%; background: var(--brand-green); flex: none; }
  .brand-sub {
    margin-top: 6px; font-size: 14px; letter-spacing: 6px;
    color: #8b8f8c; text-transform: uppercase;
  }
  .card-back .brand-sub { color: #9a9a9a; }

  /* back side */
  .card-back {
    left: 420px; top: 430px; width: 720px; height: 412px;
    background: linear-gradient(120deg, var(--card-light) 0%, #ffffff 40%, var(--card-light-shade) 100%);
  }
  .card-back .brand { position: absolute; left: 34px; top: 200px; }
  .card-back .brand-name { font-size: 36px; gap: 10px; }
  .card-back .brand-dot { width: 16px; height: 16px; }
  .card-back .brand-sub { font-size: 11px; letter-spacing: 4px; padding-left: 26px; }

  .holder { position: absolute; left: 0; right: 0; top: 36px; text-align: center; }
  .holder-name { font-size: 30px; font-weight: 700; color: var(--brand-green-deep); line-height: 1; }
  .holder-title { font-size: 14px; color: var(--ink); margin-top: 5px; }

  .divider { position: absolute; left: 352px; top: 128px; width: 1px; height: 140px; background: var(--rule); }

  .contacts { position: absolute; left: 372px; top: 128px; list-style: none; }
  .contacts li {
    display: flex; align-items: center; gap: 9px;
    font-size: 14.5px; color: var(--ink); height: 28px;
    white-space: nowrap;
  }
  .contact-icon {
    width: 18px; height: 18px; border-radius: 50%;
    background: var(--brand-green); flex: none;
    display: flex; align-items: center; justify-content: center;
  }
  .contact-icon svg { width: 11px; height: 11px; fill: #fff; }

  .website {
    position: absolute; left: 0; right: 0; bottom: 30px; text-align: center;
    font-size: 20px; font-weight: 700; letter-spacing: 1px; color: var(--ink);
  }
</style>
</head>
<body>
<main class="stage">

  <section class="card card-front" role="img" aria-label="Card front: dark faceted green-black background with Veldtmoor Capital Group name">
    <div class="brand">
      <div class="brand-name"><span class="brand-dot"></span>VELDTMOOR</div>
      <div class="brand-sub">Capital Group</div>
    </div>
  </section>

  <section class="card card-back" aria-label="Card back: contact details on light faceted background">
    <div class="holder">
      <div class="holder-name">Desmond Whitlake</div>
      <div class="holder-title">Managing Partner</div>
    </div>

    <div class="brand">
      <div class="brand-name"><span class="brand-dot"></span>VELDTMOOR</div>
      <div class="brand-sub">Capital Group</div>
    </div>

    <div class="divider"></div>

    <ul class="contacts">
      <li><span class="contact-icon"><svg viewBox="0 0 12 12"><path d="M2 1h2l1 3-1.4 1a6 6 0 0 0 3.4 3.4L8 7l3 1v2a1 1 0 0 1-1 1A9 9 0 0 1 1 2a1 1 0 0 1 1-1z"/></svg></span>415.555.0142</li>
      <li><span class="contact-icon"><svg viewBox="0 0 12 12"><path d="M3 1h5l1 1v2H3z M1 5h10v5H1z M3 7h6v1H3z"/></svg></span>415.555.0147</li>
      <li><span class="contact-icon"><svg viewBox="0 0 12 12"><path d="M3.5 0h5a1 1 0 0 1 1 1v10a1 1 0 0 1-1 1h-5a1 1 0 0 1-1-1V1a1 1 0 0 1 1-1zM4 2v7h4V2z"/></svg></span>415.555.0193</li>
      <li><span class="contact-icon"><svg viewBox="0 0 12 12"><path d="M1 3h10v6H1z M1 3l5 3.5L11 3" stroke="#1f8a3b" stroke-width="0.8"/></svg></span>desmond@veldtmoorcapital.ventures.com</li>
      <li><span class="contact-icon"><svg viewBox="0 0 12 12"><path d="M6 0a4 4 0 0 1 4 4c0 3-4 8-4 8S2 7 2 4a4 4 0 0 1 4-4zm0 2.5a1.5 1.5 0 1 0 0 3 1.5 1.5 0 0 0 0-3z"/></svg></span>187 Fenworth St San Francisco, CA 94187</li>
    </ul>

    <div class="website">www.veldtmoorcapital.ventures.com</div>
  </section>

</main>
</body>
</html>
```